Hair Salon Brochure

We need a brochure for our hair salon located in Middle Tennessee called Marla Trims of Cedar Hollow. Along with standard services, we offer specialized services and accommodations for individuals on the Autism Spectrum, regardless of background or hair type.
At Marla Trims of Cedar Hollow, our mission is to create a warm and inclusive haven for individuals of all backgrounds, including those on the autism spectrum and their families. We are dedicated to providing not only exceptional hairstyling services but also hands-on education and specialized cutting techniques for clients with natural textured hair. Our goal is to empower our clients with the knowledge and tools necessary to maintain a successful hair care routine, ensuring they leave our salon feeling confident.
We believe in fostering a sense of community, where parents of younger clients are encouraged to learn the proper hair care techniques for their children, promoting healthy practices at home. Our commitment extends beyond just hair; we are here to help you embrace your true self and recognize the beauty that resides within.
At Marla Trims of Cedar Hollow, our passion is to deliver the ultimate client experience, where you can be unapologetically yourself and feel completely at ease. From the moment you step through our doors, you are welcomed not only to discuss your hair concerns but also to engage in meaningful conversations about life. Together, we will collaborate on a personalized plan to achieve your hair goals and transform the way you perceive yourself.
Always remember, when you look good, you feel good, and when you feel good, you can achieve great things. We firmly believe that every individual is 'Beautiful Beyond the Spectrum,' and we are here to celebrate that beauty with you."
https://www.marlatrimsco.net/
Tagline - "Beautiful Beyond the Spectrum"

```html
<!DOCTYPE html>
<html lang="en">
<head>
<meta charset="utf-8">
<title>Marla Trims of Cedar Hollow – Trifold Brochure</title>
<link href="https://fonts.googleapis.com/css2?family=Comfortaa:wght@300;400;600&family=Josefin+Sans:wght@400;600&family=Kaushan+Script&display=swap" rel="stylesheet">
<style>
  :root{
    --page-bg:#d9d9d9;
    --blue-soft:#a9c8ee;
    --orange:#e8730f;
    --white:#ffffff;
    --ink-grey:#5d5d66;
    --brand-blue:#1e5fae;
    --bullet:#1d1f3a;
  }
  *{box-sizing:border-box;margin:0;padding:0}
  html,body{width:849px;height:1200px;overflow:hidden}
  body{background:var(--page-bg);position:relative;font-family:"Josefin Sans",sans-serif}
  .brochure{position:absolute;left:47px;top:331px;width:754px;height:537px;overflow:hidden;box-shadow:0 6px 18px rgba(0,0,0,.25)}
  .brochure-shapes{position:absolute;inset:0;width:754px;height:537px}
  .abs{position:absolute}

  /* left panel */
  .intro-heading{left:22px;top:29px;width:215px;font-family:"Comfortaa",sans-serif;font-weight:400;font-size:16px;line-height:20.3px;color:var(--blue-soft)}
  .mission{left:22px;top:141px;width:212px;font-size:7.9px;line-height:12.3px;color:var(--white)}

  /* middle panel */
  .tagline{left:253px;width:247px;top:22px;text-align:center;font-family:"Comfortaa",sans-serif;font-weight:400;font-size:19px;line-height:25px;color:var(--brand-blue)}
  .experience{left:253px;width:247px;top:106px;text-align:center;font-family:"Comfortaa",sans-serif;font-size:14px;line-height:21px;color:var(--ink-grey)}
  .stylist-name{left:253px;width:247px;top:271px;text-align:center;font-family:"Comfortaa",sans-serif;font-weight:600;font-size:16.5px;color:var(--white)}
  .stylist-role{left:253px;width:247px;top:292px;text-align:center;font-size:11px;color:var(--white)}
  .services-label{left:290px;top:418px;width:84px;transform:rotate(-90deg);transform-origin:left top;font-family:"Kaushan Script",cursive;font-size:21px;line-height:24px;color:var(--orange);text-align:center}
  .services-list{left:324px;top:340px;list-style:none}
  .services-list li{font-family:"Comfortaa",sans-serif;font-size:13px;line-height:22px;color:var(--white);position:relative;padding-left:15px}
  .services-list li::before{content:"";position:absolute;left:0;top:7px;width:6px;height:7px;border-radius:50%;background:var(--bullet)}
  .call-label{left:293px;top:441px;font-size:11px;color:var(--white);letter-spacing:.3px}
  .phone{left:292px;top:453px;font-family:"Comfortaa",sans-serif;font-size:23px;color:var(--white);letter-spacing:.5px}
  .contact-line{left:293px;font-family:"Comfortaa",sans-serif;font-size:12px;color:var(--white);display:flex;align-items:center;gap:8px}
  .contact-line .dot{width:12px;height:12px;border-radius:50%;background:var(--orange);flex:none}
  .handle{top:474px}
  .web{top:493px}

  /* right panel */
  .brand-name{left:500px;width:254px;top:323px;text-align:center;font-family:"Comfortaa",sans-serif;font-weight:600;font-size:15px;color:var(--white)}
  .headline{left:500px;width:254px;top:382px;text-align:center;font-family:"Kaushan Script",cursive;font-weight:400;line-height:1}
  .headline .line-one{display:block;font-size:42px;color:var(--white)}
  .headline .line-two{display:block;font-size:44px;color:var(--orange);margin-top:4px;padding-left:6px}
  .site{left:500px;width:254px;top:487px;text-align:center;font-size:11px;font-weight:600;color:var(--white)}
</style>
</head>
<body>
<main class="brochure">
  <svg class="brochure-shapes" viewBox="0 0 754 537" xmlns="http://www.w3.org/2000/svg">
    <defs>
      <linearGradient id="blueFill" x1="0" y1="0" x2="0" y2="1">
        <stop offset="0" stop-color="#1762b1"/><stop offset="1" stop-color="#0d4f9c"/>
      </linearGradient>
      <linearGradient id="purpleFill" x1="0" y1="0" x2="1" y2="1">
        <stop offset="0" stop-color="#6a42d0"/><stop offset="1" stop-color="#5729bf"/>
      </linearGradient>
      <radialGradient id="salonPhoto" cx=".55" cy=".4" r=".8">
        <stop offset="0" stop-color="#3d4a66"/><stop offset=".6" stop-color="#262b38"/><stop offset="1" stop-color="#8a6748"/>
      </radialGradient>
      <linearGradient id="warmPhoto" x1="0" y1="0" x2="1" y2="1">
        <stop offset="0" stop-color="#c49474"/><stop offset="1" stop-color="#6e4a35"/>
      </linearGradient>
      <linearGradient id="lightPhoto" x1="0" y1="0" x2="1" y2="1">
        <stop offset="0" stop-color="#efe6dd"/><stop offset="1" stop-color="#a88670"/>
      </linearGradient>
    </defs>
    <rect x="0" y="0" width="254" height="537" fill="url(#blueFill)"/>
    <rect x="254" y="0" width="246" height="260" fill="var(--white)"/>
    <rect x="500" y="0" width="254" height="260" fill="url(#salonPhoto)" role="img" aria-label="Photo: salon window with blinds, a lit heart sign and butterfly decals"/>
    <path d="M254,246 C300,234 340,230 380,236 S460,250 500,240 C560,226 620,236 680,244 S740,240 754,234 V537 H254 Z" fill="url(#purpleFill)"/>
    <path d="M254,246 C300,234 340,230 380,236 S460,250 500,240 C560,226 620,236 680,244 S740,240 754,234" fill="none" stroke="var(--orange)" stroke-width="3"/>
    <path d="M110,537 C118,470 150,420 200,402 C228,392 248,386 262,394 C280,420 284,480 281,537 Z" fill="var(--orange)"/>
    <circle cx="376" cy="207" r="58" fill="#f1f1f3"/>
    <circle cx="376" cy="207" r="51" fill="var(--white)"/>
    <circle cx="376" cy="207" r="47" fill="url(#warmPhoto)" role="img" aria-label="Portrait of the stylist"/>
    <circle cx="187" cy="413" r="55" fill="var(--white)"/>
    <circle cx="187" cy="413" r="51" fill="url(#lightPhoto)" role="img" aria-label="Photo: client having hair washed at a salon basin"/>
    <circle cx="67" cy="464" r="77" fill="var(--white)"/>
    <circle cx="67" cy="464" r="73" fill="url(#warmPhoto)" role="img" aria-label="Photo: smiling client getting a blow-dry"/>
  </svg>

  <h2 class="abs intro-heading">We offer specialized services and accommodations for individuals on the autism spectrum</h2>
  <p class="abs mission">At Marla Trims of Cedar Hollow, our mission is to create a warm and inclusive haven for individuals of all backgrounds, including those on the autism spectrum and their families. We are dedicated to providing not only exceptional hairstyling services but also hands-on education and specialized cutting techniques for clients with natural textured hair. Our goal is to empower our clients with the knowledge and tools necessary to maintain a successful hair care routine, ensuring they leave our salon feeling confident. We believe in fostering a sense of community, where parents of younger clients are encouraged to learn the proper hair care techniques for their children, promoting healthy practices at home. Our commitment extends beyond just hair; we are here to help you embrace your true self and recognize the beauty that resides within.</p>

  <p class="abs tagline">Beautiful Beyond<br>the Spectrum</p>
  <p class="abs experience">We are not just a salon,<br>we are an experience!</p>
  <h3 class="abs stylist-name">Renita Vale</h3>
  <p class="abs stylist-role">Stylist / Curl Specialist</p>
  <p class="abs services-label">Services:</p>
  <ul class="abs services-list">
    <li>Haircut and Styling</li>
    <li>Hair Coloring</li>
    <li>Hair Extensions</li>
    <li>Blowouts</li>
  </ul>
  <p class="abs call-label">CALL US</p>
  <p class="abs phone">615-555-0148</p>
  <p class="abs contact-line handle"><span class="dot"></span>@marlatrimsofch</p>
  <p class="abs contact-line web"><span class="dot"></span>www.marlatrimsco.net</p>

  <p class="abs brand-name">Marla Trims of Cedar Hollow</p>
  <h1 class="abs headline"><span class="line-one">Expert Hair</span><span class="line-two">Treatments</span></h1>
  <p class="abs site">www.marlatrimsco.net</p>
</main>
</body>
</html>
```